Brightwell Supports

We need an updated website that captures the comprehensive services and supports we provide to persons with developmental disabilities. We need a website design that educates families about the services we provide. We would also need a website that is user-friendly so that we could periodically update training schedules and ongoing programming.

• Thank you for submitting designs.  A few things I am hoping to see offered in the website:
• Front page highlights the services we offer (host homes, family caregiver, day program, employment program, SLS program, supported apartment program, behavior/clinical program)
• Front page also highlights any new programs we want to make prominent:  family caregiver, future restaurant employment openings, etc...
• Interactive Training Calendar
• Employee Resources page (link to carevo, email login, etc.)
• Uniform provider application for host home providers
• Information on agency - history, goals, etc.
• Contact Information/Location

 

Fun things to include:

• Client Highlights (featuring a client story each month, etc...)
• Employee highlights (featuring a staff member...)
• link to other Brightwell business pages (Brightwell Therapy and Brightwell Restaurant)

```html
<!DOCTYPE html>
<html lang="en">
<head>
<meta charset="utf-8">
<title>Brightwell Supports</title>
<link href="https://fonts.googleapis.com/css2?family=Open+Sans:ital,wght@0,400;0,600;1,400;1,600&display=swap" rel="stylesheet">
<style>
:root{
  --brand:#8e0000;
  --brand-dark:#7a0000;
  --text:#555555;
  --text-dark:#222222;
  --panel:#f2f2f2;
  --sidebar:#efefef;
  --rule:#dddddd;
  --footer:#4a4a4a;
  --footer-text:#c8c8c8;
  --white:#ffffff;
}
*{box-sizing:border-box;margin:0;padding:0}
html,body{width:1047px;height:1200px;overflow:hidden;background:var(--white)}
body{position:relative;font-family:"Open Sans",Arial,sans-serif;color:var(--text)}
.sidebar{position:absolute;left:62px;top:0;width:212px;height:396px;background:linear-gradient(90deg,#f7f7f7,var(--sidebar))}
.brand{position:absolute;left:18px;top:30px;display:flex;align-items:center;gap:8px}
.brand-dot{width:14px;height:14px;border-radius:50%;background:var(--brand)}
.brand-name{font-size:15px;font-weight:600;color:var(--brand)}
.nav{position:absolute;left:16px;top:86px;list-style:none}
.nav li{height:23.4px;font-size:11px;color:#444;display:flex;align-items:center}
.nav li svg{margin-right:14px}
.nav li.active{color:var(--brand);font-weight:600}
.phone{position:absolute;right:64px;top:28px;font-size:17px;color:#555}
.phone span{color:var(--brand)}
.slider{position:absolute;left:300px;top:80px;width:683px;height:316px;background:#e0e0e0;padding:4px}
.slide-photo{width:100%;height:100%;background:linear-gradient(100deg,#c9cdd3 0%,#e7e5e1 40%,#d6d7da 70%,#b9bcc2 100%)}
.caption{position:absolute;left:4px;top:119px;width:268px;height:79px;background:rgba(30,30,30,.88);clip-path:polygon(0 0,100% 0,88% 100%,0 100%);color:var(--white);font-size:16.5px;font-weight:600;line-height:20px;padding:9px 0 0 19px}
.dots{position:absolute;left:313px;top:289px;display:flex;gap:7px}
.dots i{width:10px;height:10px;border-radius:50%;background:#333}
.dots i.on{background:#c00000}
.welcome{position:absolute;left:0;top:414px;width:1047px;text-align:center}
.welcome h1{font-size:20px;font-weight:400;color:var(--brand);margin-bottom:10px}
.welcome p{font-size:11px;line-height:18.5px;color:#555}
.mission{position:absolute;left:64px;top:510px;width:919px;height:86px;background:linear-gradient(var(--brand),var(--brand-dark));border-radius:2px;color:var(--white);text-align:center;font-style:italic;padding:14px 24px 0}
.mission h2{font-size:17px;font-weight:600;margin-bottom:8px}
.mission p{font-size:12px;line-height:16px}
.section-title{position:absolute;left:66px;font-size:20px;font-weight:400;color:var(--brand)}
.pager{position:absolute;right:64px;top:624px;display:flex;gap:4px}
.card{position:absolute;top:656px;width:288px;height:148px;background:var(--panel);border-radius:2px;padding:12px 16px}
.card h3{font-size:13.5px;font-weight:600;color:var(--brand);margin-bottom:6px}
.card p{font-size:11px;line-height:16px;color:#555}
.card a{display:block;margin-top:6px;font-size:11px;font-weight:600;color:var(--text-dark);text-decoration:none}
.divider{position:absolute;left:64px;top:825px;width:919px;height:1px;background:var(--rule)}
.support-photo{position:absolute;left:64px;top:881px;width:287px;height:191px;background:linear-gradient(120deg,#8b9aa8,#c2c7cc 55%,#7d8a96)}
.support{position:absolute;width:290px}
.support h3{font-size:13.5px;font-weight:600;color:var(--brand);margin-bottom:6px}
.support p{font-size:11px;line-height:16px;color:#555}
.vrule{position:absolute;left:680px;top:881px;width:1px;height:214px;background:var(--rule)}
.hrule{position:absolute;top:966px;height:1px;background:var(--rule)}
.btn{position:absolute;left:882px;top:1066px;width:101px;height:30px;background:#6e6e6e;border:1px solid #5c5c5c;border-radius:2px;color:var(--white);font-size:11px;font-weight:600;display:flex;align-items:center;justify-content:center}
.footer{position:absolute;left:0;top:1121px;width:1047px;height:79px;background:var(--footer)}
.footer p{position:absolute;left:65px;top:22px;font-size:10px;line-height:16px;color:var(--footer-text)}
.social{position:absolute;right:64px;top:26px;display:flex;gap:6px}
.social i{width:24px;height:24px;border-radius:3px;background:#8a8a8a}
</style>
</head>
<body>
<aside class="sidebar">
  <div class="brand"><span class="brand-dot"></span><span class="brand-name">Brightwell Supports</span></div>
  <ul class="nav">
    <li class="active"><svg width="6" height="6" viewBox="0 0 6 6"><path d="M0 3h5M3 1l2 2-2 2" stroke="#8e0000" fill="none"/></svg>Welcome</li>
    <li><svg width="6" height="6" viewBox="0 0 6 6"><path d="M0 3h5M3 1l2 2-2 2" stroke="#333" fill="none"/></svg>Available Services</li>
    <li><svg width="6" height="6" viewBox="0 0 6 6"><path d="M0 3h5M3 1l2 2-2 2" stroke="#333" fill="none"/></svg>Residential Program</li>
    <li><svg width="6" height="6" viewBox="0 0 6 6"><path d="M0 3h5M3 1l2 2-2 2" stroke="#333" fill="none"/></svg>Day/Employment Program</li>
    <li><svg width="6" height="6" viewBox="0 0 6 6"><path d="M0 3h5M3 1l2 2-2 2" stroke="#333" fill="none"/></svg>SLS Program</li>
    <li><svg width="6" height="6" viewBox="0 0 6 6"><path d="M0 3h5M3 1l2 2-2 2" stroke="#333" fill="none"/></svg>Become a Provider</li>
    <li><svg width="6" height="6" viewBox="0 0 6 6"><path d="M0 3h5M3 1l2 2-2 2" stroke="#333" fill="none"/></svg>Employee Resources</li>
    <li><svg width="6" height="6" viewBox="0 0 6 6"><path d="M0 3h5M3 1l2 2-2 2" stroke="#333" fill="none"/></svg>Meet Our Team!</li>
    <li><svg width="6" height="6" viewBox="0 0 6 6"><path d="M0 3h5M3 1l2 2-2 2" stroke="#333" fill="none"/></svg>Activity Calendar</li>
    <li><svg width="6" height="6" viewBox="0 0 6 6"><path d="M0 3h5M3 1l2 2-2 2" stroke="#333" fill="none"/></svg>Training Calendar</li>
    <li><svg width="6" height="6" viewBox="0 0 6 6"><path d="M0 3h5M3 1l2 2-2 2" stroke="#333" fill="none"/></svg>Contact Us</li>
    <li><svg width="6" height="6" viewBox="0 0 6 6"><path d="M0 3h5M3 1l2 2-2 2" stroke="#333" fill="none"/></svg>Location</li>
    <li><svg width="6" height="6" viewBox="0 0 6 6"><path d="M0 3h5M3 1l2 2-2 2" stroke="#333" fill="none"/></svg>Community Resources</li>
  </ul>
</aside>

<div class="phone">Phone: <span>555-014-2287</span></div>

<section class="slider">
  <div class="slide-photo" role="img" aria-label="Group of smiling professionals in business attire"></div>
  <div class="caption">Building Abilities<br>Creating Opportunities<br>Developing Relationships</div>
  <div class="dots"><i class="on"></i><i></i><i></i><i></i></div>
</section>

<section class="welcome">
  <h1>Welcome to Brightwell Supports</h1>
  <p>Brightwell Supports is an agency designed to creatively serve individuals with developmental disabilities in community-based settings throughout Colorado.<br>Brightwell Supports is an approved service agency through the Division of Developmental Disabilities.</p>
</section>

<section class="mission">
  <h2>Mission Statement</h2>
  <p>To promote relationships, attachment, positive boundaries, and resource development to create opportunities and improve the lives of people living with disabilities.</p>
</section>

<h2 class="section-title" style="top:614px">Brightwell Supports Values</h2>
<div class="pager">
  <svg width="8" height="12" viewBox="0 0 8 12"><path d="M6 2L2 6l4 4" stroke="#333" stroke-width="2" fill="none"/></svg>
  <svg width="8" height="12" viewBox="0 0 8 12"><path d="M2 2l4 4-4 4" stroke="#333" stroke-width="2" fill="none"/></svg>
</div>

<article class="card" style="left:64px">
  <h3>Community Integration:</h3>
  <p>Promoting "connected independence" for individuals to continually develop necessary skills to live as an integrated member of their communities. Through supported employment services and resourceful providers..</p>
  <a>Read More &gt;&gt;</a>
</article>
<article class="card" style="left:379px">
  <h3>Carevoeutic Attachment:</h3>
  <p>Building solid and positive bonds among the individual with disabilities and their family members, providers and friends. Many clients have histories of trauma, abuse and/or neglect that may have interfered..</p>
  <a>Read More &gt;&gt;</a>
</article>
<article class="card" style="left:694px">
  <h3>Positive Boundaries:</h3>
  <p>Encouraging appropriate and positive limits among clients, providers and staff to create a healthy environment. Brightwell Supports continually strives toward promoting the use of firm carevoeutic boundaries to increase....</p>
  <a>Read More &gt;&gt;</a>
</article>

<div class="divider"></div>

<h2 class="section-title" style="top:840px">Client Supports</h2>
<div class="support-photo" role="img" aria-label="Smiling couple shaking hands with an advisor"></div>

<div class="support" style="left:378px;top:876px">
  <h3>Client Advisory Board</h3>
  <p>Brightwell Supports receives feedback and direction from a group of individuals comprised of persons receiving care and services from Brightwell Supports.</p>
</div>
<div class="support" style="left:692px;top:876px">
  <h3>Recreational Support</h3>
  <p>The agency supports clients to be actively involved with community events and recreation activities, including agency-sponsored events..</p>
</div>
<div class="hrule" style="left:378px;width:290px"></div>
<div class="hrule" style="left:692px;width:291px"></div>
<div class="vrule"></div>
<div class="support" style="left:378px;top:978px">
  <h3>Integrated Treatment Plans</h3>
  <p>The agency creates specialized plans that attend not only to the client's behavioral and medical needs, but also to any trauma histories and/or mental health needs.</p>
</div>
<div class="support" style="left:692px;top:978px">
  <h3>Personal Goal Plans</h3>
  <p>Brightwell Supports offers personally tailored goal plans to ensure that the agency meets the unique needs of the client.</p>
</div>
<div class="btn">Read More</div>

<footer class="footer">
  <p>Content copyright 2014. Brightwell Supports.<br>All rights reserved.</p>
  <div class="social" aria-label="Social links"><i></i><i></i><i></i><i></i></div>
</footer>
</body>
</html>
```